Stationary design and implementation for Swedish IT company

Hi,

I'm looking for a design and statiionary for my company (www.fenrolux.example).

Fenrolux is an innovative company with four core values:
- Entrepreneurial; we take risks and the responsibility to create value
- Awarding; we work with fun and have added value to our relationships
- Innovation; we're creative and introduce new solutions
- Respect; we work with respect for our environment based on values instead of red tape

The required stationary should include:
- Powerpoint template
- Word templates
- Business card design
- e-mail signature

Please visit our site for more details.

Hi - please read (PRIORITY!),

You have been involved in one my projects. 

As it seems there is something seriously wrong with the participation payments at ArtHive. 

I have send invites with participation payments to reward designers for there work. It has been reported that these invitations resulted in expired messages, and payments have NOT been made. The money is withdrawn from my account and NOT paid to designers. This is a real shame when people do not get rewarded for the work done and the money is gone.

When you got an invitation with participation payment could you please let me know if the payment has actually been made? You can contact me at mlindqvel@fenrolux.example.

I'm trying to get this clarified with ArtHive.

Grt, Nils

Target Market(s)

Our market is IT and professional service in Sweden and other Nordics countries (Danmark, Norway, Finland).

Industry/Entity Type

Environment

Requirements
Must have
• Project delivery should include:
- Powerpoint template with title and content pages
- Standard letter (Word template)
- Standard invoice (Word template)
- Business card
- e-mail signature
Should not have
• Please await a logo to be attached (almost done).

```html
<!DOCTYPE html>
<html lang="en">
<head>
<meta charset="utf-8">
<title>Fenrolux Stationery</title>
<link href="https://fonts.googleapis.com/css2?family=Open+Sans:wght@400;600;700&display=swap" rel="stylesheet">
<style>
  :root {
    --paper: #ffffff;
    --page-bg: #ffffff;
    --ink: #222222;
    --brand-blue: #2f4a9c;
    --slide-blue: #2b3a8f;
    --frame: #b9b9b9;
    --rule-dark: #333333;
    --rule-soft: #9a9a9a;
    --orange-light: #f7b36a;
    --orange-deep: #e8812b;
  }
  * { box-sizing: border-box; margin: 0; padding: 0; }
  html, body {
    width: 1200px; height: 900px; overflow: hidden;
    background: var(--page-bg);
    font-family: "Open Sans", Arial, sans-serif;
    color: var(--ink);
  }
  .canvas { position: relative; width: 1200px; height: 900px; }

  .sheet {
    position: absolute;
    background: var(--paper);
    border: 1px solid var(--frame);
  }

  .brand { position: absolute; display: flex; align-items: center; gap: 0.3em; }
  .brand-dot { border-radius: 50%; background: var(--brand-blue); flex: none; }
  .brand-name { color: var(--brand-blue); font-weight: 400; line-height: 1; letter-spacing: -0.01em; }

  .swoosh-line {
    position: absolute; width: 3px;
    background: linear-gradient(to bottom, rgba(150,150,150,0), #8f8f8f 30%, #8f8f8f 70%, rgba(150,150,150,0));
    border-radius: 2px;
  }

  /* Business card */
  .business-card { left: 24px; top: 24px; width: 532px; height: 296px; }
  .business-card .contact { position: absolute; right: 314px; text-align: right; white-space: nowrap; }
  .business-card .contact-name { top: 58px; font-size: 18px; }
  .business-card .contact-email { top: 90px; font-size: 14px; }
  .business-card .contact-phone { top: 154px; font-size: 12px; }
  .business-card .contact-address { top: 190px; font-size: 12px; }
  .business-card .swoosh-line { left: 232px; top: 16px; height: 262px; }
  .business-card .brand { left: 246px; top: 104px; }
  .business-card .brand-dot { width: 40px; height: 40px; }
  .business-card .brand-name { font-size: 50px; }

  /* Email signature */
  .email-signature { left: 134px; top: 356px; width: 292px; height: 204px; }
  .email-signature .swoosh-line { left: 34px; top: 14px; height: 92px; }
  .email-signature .sig-name { position: absolute; left: 48px; top: 22px; font-size: 16px; }
  .email-signature .sig-role { position: absolute; left: 48px; top: 42px; font-size: 11px; }
  .email-signature .sig-email { position: absolute; left: 48px; top: 72px; font-size: 12px; }
  .email-signature .divider { position: absolute; left: 6px; top: 116px; width: 280px; height: 2px; background: var(--rule-dark); }
  .email-signature .brand { left: 22px; top: 132px; }
  .email-signature .brand-dot { width: 34px; height: 34px; }
  .email-signature .brand-name { font-size: 44px; }

  /* Presentation slide */
  .title-slide { left: 76px; top: 594px; width: 430px; height: 280px; overflow: hidden; }
  .title-slide .hero-band { position: absolute; left: 0; top: 0; width: 100%; height: 216px; background: var(--slide-blue); }
  .title-slide .hero-art {
    position: absolute; left: 134px; top: 50px; width: 140px; height: 146px;
    border-radius: 28px 50px 50px 20px;
    background: linear-gradient(160deg, var(--orange-light), var(--orange-deep));
  }
  .title-slide .brand { left: 14px; top: 224px; }
  .title-slide .brand-dot { width: 26px; height: 26px; }
  .title-slide .brand-name { font-size: 34px; }

  /* Letterhead */
  .letterhead { left: 592px; top: 80px; width: 584px; height: 750px; }
  .letterhead .brand { left: 76px; top: 34px; }
  .letterhead .brand-dot { width: 22px; height: 22px; }
  .letterhead .brand-name { font-size: 28px; }
  .letterhead .footer-rule { position: absolute; left: 72px; top: 690px; width: 446px; height: 1px; background: var(--rule-soft); }
  .letterhead .footer-address {
    position: absolute; right: 70px; top: 696px;
    font-size: 8px; font-weight: 600; color: #555555; white-space: nowrap;
  }
</style>
</head>
<body>
<main class="canvas">

  <section class="sheet business-card" aria-label="Business card">
    <p class="contact contact-name">Your name</p>
    <p class="contact contact-email">email@yourdomain.com</p>
    <p class="contact contact-phone">Your telephone</p>
    <p class="contact contact-address">Your Address</p>
    <span class="swoosh-line"></span>
    <div class="brand"><span class="brand-dot"></span><span class="brand-name">Fenrolux</span></div>
  </section>

  <section class="sheet email-signature" aria-label="E-mail signature">
    <span class="swoosh-line"></span>
    <p class="sig-name">Your name</p>
    <p class="sig-role">Director</p>
    <p class="sig-email">email@yourdomain.com</p>
    <span class="divider"></span>
    <div class="brand"><span class="brand-dot"></span><span class="brand-name">Fenrolux</span></div>
  </section>

  <section class="sheet title-slide" aria-label="Presentation title slide">
    <div class="hero-band"></div>
    <div class="hero-art" role="img" aria-label="Orange glossy presentation illustration"></div>
    <div class="brand"><span class="brand-dot"></span><span class="brand-name">Fenrolux</span></div>
  </section>

  <section class="sheet letterhead" aria-label="Letterhead">
    <div class="brand"><span class="brand-dot"></span><span class="brand-name">Fenrolux</span></div>
    <span class="footer-rule"></span>
    <p class="footer-address">Unit 12, 8 Harrowgate Lane, Linmouth, Sweden, LN4 7QA</p>
  </section>

</main>
</body>
</html>
```